Lantern Petals Website v.1 - attract floral shop franchisees

I need a simple information website for my new business. We are a franchisor of flower shops. The overall purpose of the website is to promote the company and the service, especially to potential franchisees and retailers. Only about 4 pages are required including homepage, About, For Supermarkets, For Franchisees, and Contact. No special functions are required except the site will have two separate inquiry forms that must be filled out online and submitted via automated email. Similarly, an email form should be linked from the Contact page. I have a logo and business cards designed by ArtMingle, and I would like the site to have a consistent color scheme and style. The key to design will be to express the joy and love associated with flowers and floral bouquets.
IMPORTANT - I will be exporting the website design to Wordpress CMS in a site hosted by HostNimbus. For smooth integration into WordPress hosted by HostNimbus, the designer should build the site using a WordPress-friendly format. Ideally, they should use HTML, CSS, and PHP. Creating a custom theme or using a page builder that exports to WordPress-compatible files is best. This ensures the site can be easily imported and managed within WordPress.

Target Market(s)

Potential franchisees (existing florists or creative types who might like to own a floral business) and supermarkets who might want us to run their floral department

Industry/Entity Type

Floral retailing

Requirements
Must have
• A brand theme that is beautiful, consistent throughout and builds on the logo design
Nice to have
• Show gender and ethnic diversity in customers and florists. Pictures of happy florists (for franchisees) and pictures of amazing floral department displays (for supermarkets)

```html
<!DOCTYPE html>
<html lang="en">
<head>
<meta charset="utf-8">
<title>Lantern Petals</title>
<link href="https://fonts.googleapis.com/css2?family=Pinyon+Script&family=Poppins:wght@300;400;500&display=swap" rel="stylesheet">
<style>
:root{
  --blush:#f5e6e7;
  --honey:#f2b332;
  --leaf:#3a9a5b;
  --mist:#dbe7eb;
  --ink:#1e1e1e;
  --muted:#7a7a7a;
  --card:#f4f4f4;
  --white:#ffffff;
}
*{box-sizing:border-box;margin:0;padding:0}
html,body{width:1200px;height:3284px;overflow:hidden}
body{position:relative;background:var(--white);font-family:'Poppins',sans-serif;color:var(--ink)}
.abs{position:absolute}
.script{font-family:'Pinyon Script',cursive;font-weight:400;color:var(--ink);line-height:1}
.btn{position:absolute;display:flex;align-items:center;justify-content:center;background:var(--honey);color:var(--ink);border-radius:22px;font-size:13px;font-weight:500;letter-spacing:3px;width:150px;height:41px;text-decoration:none}
.body-text{font-weight:300;color:var(--muted)}

/* hero */
.hero-bg{left:0;top:0;width:1200px;height:720px}
.brand{left:28px;top:30px;display:flex;align-items:center;gap:10px;font-size:22px;font-weight:500;color:var(--honey)}
.brand-dot{width:30px;height:30px;border-radius:50%;background:var(--honey)}
.nav{left:272px;top:56px;display:flex;font-size:13.5px;letter-spacing:3px;font-weight:400}
.nav a{color:var(--ink);text-decoration:none;position:absolute;white-space:nowrap}
.hero-title{left:55px;top:210px;font-size:66px}
.hero-copy{left:55px;top:290px;width:500px;font-size:14px;line-height:21px}
.hero-art{left:585px;top:100px;width:615px;height:590px;border-radius:46% 40% 30% 30%;background:radial-gradient(circle at 55% 40%,#f7a9c3,#f3d3dc 55%,#ecdfe2 80%)}

/* about */
.ring{border-radius:50%;border:8px solid var(--leaf)}
.photo-main{left:65px;top:793px;width:385px;height:385px;background:radial-gradient(circle at 40% 40%,#e98aa0,#b8556a 60%,#6d7a55)}
.photo-second{left:237px;top:965px;width:308px;height:308px;border-radius:50%;border:6px solid var(--white);background:linear-gradient(160deg,#d7e1b4,#9ea88a 55%,#e7cf5a)}
.section-title{font-size:52px}
.about-copy{left:591px;top:902px;width:548px;font-size:13.4px;line-height:19.8px}
.about-copy p+p{margin-top:20px}

/* partner */
.mist{left:0;top:1400px;width:1200px;height:740px}
.bouquet{left:190px;top:1363px;width:450px;height:355px;border-radius:50% 45% 40% 50%;background:radial-gradient(circle at 55% 55%,#f4a7bd,#e9cdd4 50%,rgba(90,110,70,.55) 85%,transparent 100%)}
.partner-copy{left:200px;top:1746px;width:740px;text-align:center;font-size:17px;line-height:25.5px}
.partner-mark{left:527px;top:1908px;width:74px;height:74px;background:#ecdcd8}
.photo-fruit{left:845px;top:1840px;width:296px;height:296px;background:radial-gradient(circle at 40% 50%,#f0c33a,#b9602d 50%,#5c3a22 80%)}

/* cards */
.card{width:470px;height:252px;background:var(--card);top:2258px}
.card .script{position:absolute;left:37px;top:30px;font-size:46px}
.card .body-text{position:absolute;left:37px;top:92px;width:390px;font-size:15.5px;line-height:22.5px}
.card .btn{left:37px;top:182px}

/* footer */
.foot-bg{left:0;top:2640px;width:1200px;height:644px}
.foot-title{font-size:46px}
.foot-links{left:115px;top:2915px;list-style:none}
.foot-links li{font-size:15px;letter-spacing:3.5px;height:49px}
.contact-row{left:373px;display:flex;align-items:center;gap:17px;font-size:15.5px}
.icon{width:40px;height:40px;border-radius:50%;border:2px solid var(--leaf);display:flex;align-items:center;justify-content:center}
.newsletter{left:684px;top:2818px;width:452px;height:276px;background:var(--white)}
.news-input{position:absolute;left:26px;top:112px;width:282px;height:51px;border:1.5px solid #444;border-radius:26px;font-size:15px;color:var(--muted);padding-left:34px;display:flex;align-items:center;font-weight:300}
.news-btn{position:absolute;left:26px;top:187px;width:282px;height:51px;border-radius:26px;background:var(--leaf);color:var(--white);font-size:17px;letter-spacing:4px;display:flex;align-items:center;justify-content:center}
.news-art{position:absolute;right:0;top:62px;width:141px;height:214px;background:linear-gradient(180deg,#f2c6d2,#d9a9b4 45%,#c9d7d4 75%,#e7d9cf)}
.rule{left:115px;top:3183px;width:1013px;height:1px;background:#cfc3c4}
.copyright{left:0;top:3218px;width:1200px;text-align:center;font-size:15px}
</style>
</head>
<body>

<!-- hero -->
<svg class="abs hero-bg" viewBox="0 0 1200 720" aria-hidden="true">
  <path fill="var(--blush)" d="M0 0H1200V680C1150 670 1120 690 1080 676C1040 660 990 700 930 684C880 670 850 700 790 694C730 690 690 640 640 626C600 612 580 600 560 640C540 680 480 690 420 700C360 705 300 690 240 686C180 680 130 660 90 640C60 625 30 640 0 628Z"/>
</svg>
<div class="abs brand"><span class="brand-dot"></span>Lantern Petals</div>
<nav class="abs nav">
  <a style="left:0">HOME</a>
  <a style="left:96px">ABOUT</a>
  <a style="left:206px">FOR SUPERMARKETS</a>
  <a style="left:452px">FOR FRANCHISEES</a>
</nav>
<a class="btn" style="left:980px;top:44px">CONTACT</a>

<h1 class="abs script hero-title">Lantern Petals</h1>
<p class="abs body-text hero-copy">Fresh flowers convey beauty and love, and in our view should become something every person regularly enjoys. Lantern Petals is an entrepreneurial company created to make top quality fresh flowers and professionally-designed bouquets accessible to every consumer at affordable prices.</p>
<a class="btn" style="left:55px;top:427px">CONTACT</a>
<div class="abs hero-art" role="img" aria-label="Pink and white gerbera daisies with leaves in a speckled pink pot"></div>

<!-- about -->
<div class="abs ring photo-main" role="img" aria-label="Florist shop display of mixed roses and bouquets"></div>
<div class="abs photo-second" role="img" aria-label="Florist holding bouquets of yellow roses and hydrangeas in a workroom"></div>
<h2 class="abs script section-title" style="left:620px;top:820px">About</h2>
<div class="abs body-text about-copy">
  <p>Professional florists typically sell the finest quality stems, design the most beautiful bouquets and provide the finest customer service, but their costs – of floral products, retail spaces, labor and marketing – force them to pass high prices along to customers. Supermarket flower departments benefit from high customer footfall, economies of scale and low pricing, but their quality of stems and bouquets is typically poor, staffing is limited, and staff turnover is high which can result in inefficiency, wastage, poorly merchandised selections and limited service.</p>
  <p>Lantern Petals brings the best of professional florists and supermarkets together for the benefit of consumers. It supports a national network of owner-operator franchisees, who in many cases are multi-site professional florists, with comprehensive services to enhance franchise profitability. Lantern Petals works with some of the country's largest and most progressive supermarkets to provide franchisee ownership and operation of their strategically important floral departments. Supermarkets find that Lantern Petals is able to improve their financial outcomes, provide attentive customer service and satisfaction, and lift the quality of the entire store environment.</p>
</div>
<a class="btn" style="left:592px;top:1268px">CONTACT</a>

<!-- partner -->
<svg class="abs mist" viewBox="0 0 1200 740" aria-hidden="true">
  <path fill="var(--mist)" d="M480 20C540 0 560 60 600 80C660 110 720 150 800 160C880 170 960 190 1040 220C1100 240 1160 250 1200 260V430C1140 440 1100 470 1060 500C1010 540 960 560 900 580C840 600 760 610 700 640C640 670 560 660 500 650C440 640 400 680 360 700C330 716 320 690 330 660C340 630 300 600 260 580C220 560 180 520 140 490C100 460 60 440 0 430V300C60 280 100 280 150 260C200 240 250 190 300 150C350 110 420 40 480 20Z"/>
</svg>
<div class="abs bouquet" role="img" aria-label="Pink gerberas, roses and lisianthus with green leaves"></div>
<h2 class="abs script section-title" style="left:575px;top:1665px">Frostline</h2>
<p class="abs body-text partner-copy">Lantern Petals operates in partnership with Frostline Group, the leading franchisor of sushi stations and pre-packaged fruit &amp; vegetable departments to supermarkets across the United States and United Kingdom. Lantern Petals' combination of floral and supermarket franchising expertise guarantees that consumers, franchisees and supermarket partners each receive exceptional service and value.</p>
<div class="abs partner-mark"></div>
<div class="abs ring photo-fruit" role="img" aria-label="Fruit skewer tower beside a chocolate fountain"></div>

<!-- cards -->
<div class="abs card" style="left:105px">
  <h3 class="script">For Supermarkets</h3>
  <p class="body-text">Lantern Petals works with some of the country's largest and most progressive supermarkets to provide franchisee ownership</p>
  <a class="btn">READ MORE</a>
</div>
<div class="abs card" style="left:624px">
  <h3 class="script">For Franchisee</h3>
  <p class="body-text">Lantern Petals works with some of the country's largest and most progressive supermarkets to provide franchisee ownership</p>
  <a class="btn">READ MORE</a>
</div>

<!-- footer -->
<svg class="abs foot-bg" viewBox="0 0 1200 644" aria-hidden="true">
  <path fill="var(--blush)" d="M0 40C40 20 80 50 130 46C190 40 230 70 300 66C360 62 400 30 470 40C530 50 560 90 620 80C680 70 720 50 780 60C840 70 880 100 940 90C1000 80 1040 40 1100 50C1150 58 1180 80 1200 76V644H0Z"/>
</svg>
<h2 class="abs script foot-title" style="left:90px;top:2828px">About</h2>
<ul class="abs foot-links">
  <li>HOME</li><li>ABOUT</li><li>FOR SUPERMARKETS</li><li>FOR FRANCHISEE</li><li>CONTACT</li>
</ul>
<h2 class="abs script foot-title" style="left:375px;top:2828px">Contact</h2>
<div class="abs contact-row" style="top:2910px">
  <span class="icon"><svg width="18" height="18" viewBox="0 0 24 24"><path fill="var(--leaf)" d="M6.6 10.8a15.1 15.1 0 0 0 6.6 6.6l2.2-2.2c.3-.3.7-.4 1-.2 1.1.4 2.3.6 3.6.6.6 0 1 .4 1 1V20c0 .6-.4 1-1 1A17 17 0 0 1 3 4c0-.6.4-1 1-1h3.5c.6 0 1 .4 1 1 0 1.3.2 2.5.6 3.6.1.3 0 .7-.2 1z"/></svg></span>
  +1 555 014 2287
</div>
<div class="abs contact-row" style="top:2970px">
  <span class="icon"><svg width="18" height="18" viewBox="0 0 24 24"><path fill="var(--leaf)" d="M3 6h18v12H3z"/><path fill="none" stroke="#fff" stroke-width="1.6" d="M3 6l9 7 9-7"/></svg></span>
  info@Lantern-Petals.com
</div>
<div class="abs newsletter">
  <h2 class="script foot-title" style="position:absolute;left:46px;top:30px">Newsletter</h2>
  <div class="news-input">Email Address</div>
  <div class="news-btn">SUBSCRIBE NOW</div>
  <div class="news-art" role="img" aria-label="Pink bouquet in a pale blue jug"></div>
</div>
<div class="abs rule"></div>
<p class="abs copyright">Copyright 2024 Lantern Petals. All Rights Reserved.</p>

</body>
</html>
```